Website Design Request - Management Consulting Firm

We need a Website designed for an IT Management Staffing and Recruiting firm called TRAVENOK based in San Francisco.

The firm is an high-end technology staffing agency. Our focus is on quality and high-caliber candidates rather than quantity.

The website will have two main home pages. One for the recruiter and another on for the candidates.

The website needs to optimize for mobile devices as well.

I have attached few mock-ups that I have done just to show what I am thinking. The UI needs to be very clean, fluid, and it needs to have a modern, rustic, professional feel to it.

Target Market(s)

Technology Manager, Director, VP, CIO of Companies that have $4b-10b dollar revenue. Such as larkspurdwellings.example , https://www.velmorian.example/, quillnet.example, zib.example

Industry/Entity Type

Management Consulting

Number of Pages Required

5+ page

Font styles to use
Sans Serif

Colors
f37122
ffffff

Requirements
Must have
• Please review mock-ups for suggestions
Nice to have
Should not have

```html
<!DOCTYPE html>
<html lang="en">
<head>
<meta charset="utf-8">
<title>TRAVENOK – IT Project Management Jobs</title>
<link href="https://fonts.googleapis.com/css2?family=Open+Sans:wght@400;600;700;800&display=swap" rel="stylesheet">
<style>
:root{
  --orange:#f37122;
  --white:#ffffff;
  --ink:#2b2b2b;
  --muted:#777777;
  --dark:#2e3238;
  --footer:#eeeeee;
  --footer-bar:#e2e2e2;
  --green:#7cb342;
  --amber:#f5a623;
  --red:#e53935;
  --navy:#2f4a6e;
}
*{margin:0;padding:0;box-sizing:border-box}
html,body{width:900px;height:1200px;overflow:hidden}
body{font-family:'Open Sans',sans-serif;color:var(--ink);background:var(--white);position:relative}

.site-header{height:60px;display:flex;align-items:center;justify-content:space-between;padding:0 40px 0 38px;background:var(--white)}
.brand{display:flex;flex-direction:column}
.brand-name{font-size:24px;font-weight:800;color:var(--orange);letter-spacing:1px;line-height:1}
.brand-tag{font-size:7px;color:var(--muted);letter-spacing:1px;margin-top:3px}
.main-nav{display:flex;gap:0}
.main-nav a{display:block;font-size:10px;font-weight:600;color:var(--ink);text-decoration:none;padding:22px 21px;letter-spacing:.5px}
.main-nav a.active{color:var(--orange);border-bottom:2px solid var(--orange)}

.hero{position:relative;height:380px;text-align:center;color:var(--white)}
.hero-photo{position:absolute;inset:0;background:linear-gradient(180deg,#3a3f46 0%,#4d535b 45%,#6e6a66 75%,#8d8781 100%)}
.hero-content{position:relative;padding-top:88px}
.hero h1{font-size:27px;font-weight:800;letter-spacing:.5px}
.hero .lead{font-size:19px;font-weight:400;margin-top:4px}
.signup{display:flex;justify-content:center;gap:10px;margin-top:34px}
.signup .field{width:196px;height:30px;border:1px solid rgba(255,255,255,.55);background:rgba(255,255,255,.08);font-size:9px;color:rgba(255,255,255,.7);text-align:left;padding:9px 10px}
.signup .cta{height:30px;padding:0 16px;background:var(--orange);color:var(--white);font-size:9px;font-weight:700;display:flex;align-items:center;letter-spacing:.5px}
.hero .note{font-size:8px;color:rgba(255,255,255,.7);margin-top:14px}

.tabs{display:flex;height:45px}
.tab{flex:1;display:flex;align-items:center;justify-content:center;font-size:12px;font-weight:700;color:var(--white);letter-spacing:.5px}
.tab.how{background:var(--dark)}
.tab.why{background:var(--orange)}

.benefits{padding-top:40px}
.section-title{text-align:center;font-size:22px;font-weight:600;color:var(--ink)}
.section-title::after{content:"";display:block;width:56px;height:2px;background:var(--orange);margin:8px auto 0}
.benefit-grid{display:grid;grid-template-columns:1fr 1fr;column-gap:50px;row-gap:40px;padding:40px 110px 0 96px}
.benefit{display:flex;gap:20px}
.benefit .icon{flex:0 0 60px;height:60px}
.benefit h3{font-size:12px;font-weight:700;margin-top:4px;letter-spacing:.3px}
.benefit p{font-size:8px;line-height:13px;color:var(--muted);margin-top:6px}

.upload{display:flex;justify-content:center;margin-top:50px}
.upload .btn{display:flex;align-items:center;gap:8px;border:1px solid var(--orange);color:var(--orange);font-size:9px;font-weight:700;padding:8px 16px;letter-spacing:.5px}

.site-footer{position:absolute;left:0;top:960px;width:900px;height:240px;background:var(--footer)}
.footer-cols{display:flex;padding:36px 40px 0 92px}
.contact{width:310px;text-align:center}
.footer-cols h4{font-size:10px;font-weight:700;color:var(--ink);letter-spacing:.5px}
.contact .phone{font-size:22px;font-weight:700;margin-top:6px}
.contact .ask{font-size:8px;color:var(--muted);margin-top:12px}
.contact .ask b{color:var(--orange)}
.contact .callback{font-size:8px;color:var(--muted);margin-top:3px}
.contact .callback b{color:var(--orange)}
.links{width:150px;margin-left:10px}
.links ul{list-style:none;margin-top:8px}
.links li{font-size:8px;color:var(--muted);line-height:14px}
.footer-bar{position:absolute;left:0;bottom:0;width:900px;height:30px;background:var(--footer-bar);display:flex;align-items:center;justify-content:center;font-size:7px;color:var(--muted)}
.footer-bar .top{position:absolute;right:22px;font-weight:700;color:var(--ink)}
</style>
</head>
<body>

<header class="site-header">
  <div class="brand">
    <span class="brand-name">TRAVENOK</span>
    <span class="brand-tag">PROJECT MANAGEMENT CONSULTING</span>
  </div>
  <nav class="main-nav">
    <a class="active" href="#">HOME</a>
    <a href="#">PROFESSIONALS</a>
    <a href="#">EMPLOYERS</a>
    <a href="#">SIGN IN</a>
    <a href="#">SIGN UP</a>
  </nav>
</header>

<section class="hero">
  <div class="hero-photo" role="img" aria-label="Photo of a team meeting around a desk with laptops and papers"></div>
  <div class="hero-content">
    <h1>LOOKING FOR IT PROJECT MANAGEMENT JOBS?</h1>
    <p class="lead">Upload your resume, accept interview requests, get offers</p>
    <div class="signup">
      <div class="field">Your Email Address</div>
      <div class="cta">GET OFFERS NOW</div>
    </div>
    <p class="note">We never share your information</p>
  </div>
</section>

<div class="tabs">
  <div class="tab how">HOW IT WORKS</div>
  <div class="tab why">WHY US</div>
</div>

<section class="benefits">
  <h2 class="section-title">Why Professionals Love us</h2>
  <div class="benefit-grid">
    <div class="benefit">
      <svg class="icon" viewBox="0 0 60 60"><circle cx="30" cy="30" r="30" fill="var(--green)"/><text x="30" y="40" text-anchor="middle" font-family="Open Sans,sans-serif" font-size="28" font-weight="700" fill="#fff">$</text></svg>
      <div><h3>GET PAID MORE</h3><p>On average, TRAVENOK candidates get paid 20% more for their skills. Our client-focused roles are benchmarked for your niche project experience.</p></div>
    </div>
    <div class="benefit">
      <svg class="icon" viewBox="0 0 60 60"><circle cx="30" cy="30" r="30" fill="var(--amber)"/><rect x="22" y="14" width="16" height="32" rx="3" fill="#fff"/><rect x="24.5" y="18" width="11" height="22" fill="var(--amber)"/><circle cx="30" cy="43" r="1.5" fill="var(--amber)"/></svg>
      <div><h3>LESS INTERVIEWS</h3><p>Skip endless interviews with TRAVENOK to get the right job. Our vetted matches put agencies and recruiters ahead so you interview less and offer more.</p></div>
    </div>
    <div class="benefit">
      <svg class="icon" viewBox="0 0 60 60"><circle cx="30" cy="30" r="30" fill="var(--navy)"/><circle cx="30" cy="30" r="17" fill="#fff"/><circle cx="30" cy="30" r="12" fill="var(--red)"/><circle cx="30" cy="30" r="7" fill="#fff"/><circle cx="30" cy="30" r="3" fill="var(--red)"/></svg>
      <div><h3>TRANSPARENCY</h3><p>In order to provide services focused on our clients and candidates, we operate 100% transparency in all our services.</p></div>
    </div>
    <div class="benefit">
      <svg class="icon" viewBox="0 0 60 60"><circle cx="30" cy="30" r="30" fill="var(--navy)"/><path d="M18 28h6v14h-6z M26 28l6-11c3 0 4 2 3 5l-1 4h7c2 0 3 2 2 4l-3 10c-1 2-2 2-3 2H26z" fill="#fff"/></svg>
      <div><h3>MAKE BETTER DECISIONS</h3><p>Employers who have considered all their options and more. You make a decision to join us understand that we bring the highest caliber candidates for the job.</p></div>
    </div>
  </div>
  <div class="upload">
    <div class="btn">
      <svg width="12" height="12" viewBox="0 0 12 12"><path d="M6 1v7M3 4l3-3 3 3M1 9v2h10V9" stroke="var(--orange)" stroke-width="1.4" fill="none"/></svg>
      UPLOAD YOUR RESUME
    </div>
  </div>
</section>

<footer class="site-footer">
  <div class="footer-cols">
    <div class="contact">
      <h4>CONTACT US:</h4>
      <div class="phone">+(555) 014 2290</div>
      <p class="ask">HAVE QUESTIONS? <b>CALL US NOW</b></p>
      <p class="callback">OR <b>REQUEST A CALL BACK</b></p>
    </div>
    <div class="links"><h4>QUICK LINK</h4><ul><li>Team</li><li>Reviews</li><li>Blog</li><li>Contact</li></ul></div>
    <div class="links"><h4>INFORMATION</h4><ul><li>Terms and Condition</li><li>Privacy policy</li><li>Site Map</li></ul></div>
    <div class="links"><h4>COMPANY</h4><ul><li>Why Us</li><li>Contact</li><li>Customers</li><li>Affiliates</li></ul></div>
  </div>
  <div class="footer-bar">Copyright@2015 Company Name. All Rights Reserved<span class="top">TOP</span></div>
</footer>

</body>
</html>
```